We need a Welcome Booklet designed for our Church - Harrowgate Fields Church. We would like a design that is contemporary with no religious symbols or old pictures. Please use quality contemporary photos . See attached a Word document with what content we want in the booklet.

Target Market(s)

Guests to the church so new person friendly

Requirements
Must have
• A contemporary modern look
Should not have
• Religious symbols or old pictures

```html
<!DOCTYPE html>
<html lang="en">
<head>
<meta charset="utf-8">
<title>Welcome – Harrowgate Fields Church</title>
<link rel="stylesheet" href="https://fonts.googleapis.com/css2?family=Merriweather:wght@300&family=Didact+Gothic&family=Poppins:wght@600&display=swap">
<style>
  :root {
    --page: #ffffff;
    --ink: #231f20;
    --white: #ffffff;
    --sky: #3a8eea;
    --plum: #93168e;
    --hall-dark: #0d1322;
    --hall-mid: #2a3150;
    --hall-glow: #6c5a48;
    --portrait-light: #efe7da;
    --portrait-mid: #cfc2b0;
  }
  * { box-sizing: border-box; margin: 0; padding: 0; }
  html, body { width: 855px; height: 1200px; overflow: hidden; background: var(--page); }
  .page { position: relative; width: 855px; height: 1200px; overflow: hidden; }

  .hero {
    position: absolute; left: 0; top: 0; width: 855px; height: 199px;
    background: linear-gradient(90deg, var(--hall-dark) 0%, var(--hall-mid) 20%, var(--hall-glow) 55%, var(--hall-mid) 80%, var(--hall-dark) 100%);
  }
  .hero-title {
    position: absolute; left: 78px; top: 96px;
    font-family: "Merriweather", Georgia, serif; font-weight: 300;
    font-size: 44px; line-height: 1; color: var(--white);
  }

  .intro {
    position: absolute; left: 54px; top: 250px; width: 648px;
    font-family: "Didact Gothic", "Century Gothic", sans-serif;
    font-size: 25.5px; line-height: 35.6px; color: var(--ink);
    text-align: justify; text-align-last: left;
  }
  .intro p + p { margin-top: 35px; }

  .portrait {
    position: absolute; left: 363px; top: 673px; width: 411px; height: 341px;
    background: linear-gradient(180deg, var(--portrait-light) 0%, var(--portrait-mid) 100%);
  }

  .bubble {
    position: absolute; border-radius: 50%; border: 5px solid var(--white);
    display: flex; align-items: center; justify-content: center; text-align: center;
    font-family: "Poppins", "Century Gothic", sans-serif; font-weight: 600; color: var(--white);
  }
  .bubble-main {
    left: 63px; top: 658px; width: 330px; height: 330px; background: var(--sky);
    font-size: 33px; line-height: 42px; padding-top: 0;
  }
  .bubble-sign {
    left: 254px; top: 933px; width: 190px; height: 190px; background: var(--plum);
    font-size: 24px; line-height: 31.5px;
  }
</style>
</head>
<body>
<div class="page">
  <header class="hero" role="img" aria-label="Photo of a large congregation gathered in a dimly lit auditorium with blue stage lights">
    <h1 class="hero-title">Welcome</h1>
  </header>

  <section class="intro">
    <p>A very warm welcome to HFC, we are glad that you are here. If this is your first visit with us or you are a new believer and are looking for a place where you can grow in faith, please introduce yourself to any of our ministers or go to our guest lounge which is located in the Life Café.</p>
    <p>We have friendly and dedicated hosts in the green polo shirts that are ready to help you find your place and answer any questions you may have.</p>
  </section>

  <div class="portrait" role="img" aria-label="Photo of the senior ministers, a smiling couple standing together against a light wall"></div>

  <div class="bubble bubble-main"><p>We look<br>forward<br>to speaking<br>with you and<br>getting to<br>know you.</p></div>
  <div class="bubble bubble-sign"><p>Warm<br>greetings!<br>Paul and<br>Jenny<br>Whitley</p></div>
</div>
</body>
</html>
```